Product Label with Company Logo & Product Information

I am looking for a new label design for one of my products, Candied Pecans. I am including an old label that I made, but it does not "pop" on the current packaging. See image of current packaging attached as well.

I want the design to ultimately be something that I can take and order a roll of labels/stickers. Please stick within standard label/sticker sizes (round or square). Please include final size as well.

Must Haves:
(1) Company logo (any color variation-see attached logo images).
(2) All wording on the old label
(3) Label size can not be more than 2 in. x 4 in. (I would actually like them a little smaller). They seem kind of big as they are right now.

```html
<!DOCTYPE html>
<html lang="en">
<head>
<meta charset="utf-8">
<title>Amber Comb – Gourmet Candied Pecans Label</title>
<link rel="stylesheet" href="https://fonts.googleapis.com/css2?family=Cinzel:wght@600&family=Pirata+One&family=Playfair+Display:wght@700&family=Roboto:wght@700&display=swap">
<style>
  :root {
    --backdrop: #232323;
    --label-bg: #202024;
    --frame: #6a6a6e;
    --comb: #2c2c31;
    --comb-edge: #38383e;
    --ornament: #55555a;
    --honey: #f1e52a;
    --title-grey: #58585c;
    --copy-grey: #6c6c70;
  }
  * { margin: 0; padding: 0; box-sizing: border-box; }
  html, body { width: 1200px; height: 780px; overflow: hidden; background: var(--backdrop); }
  .canvas { position: relative; width: 1200px; height: 780px; }
  .label {
    position: absolute; left: 107px; top: 138px; width: 1012px; height: 506px;
    background: var(--label-bg);
  }
  .label-frame { position: absolute; inset: 0; }
  .comb-area { position: absolute; }
  .comb-area--top { left: 34px; top: 31px; width: 277px; height: 181px; }
  .comb-area--bottom { left: 707px; top: 293px; width: 277px; height: 181px; }
  .brand {
    position: absolute; left: 0; right: 0; top: 72px;
    display: flex; align-items: center; justify-content: center; gap: 10px;
    font-family: "Cinzel", serif; font-weight: 600; font-size: 30px; color: var(--honey);
  }
  .brand-dot { width: 22px; height: 22px; border-radius: 50%; background: var(--honey); }
  .text-block { position: absolute; left: 0; right: 0; text-align: center; }
  .title {
    top: 200px; font-family: "Playfair Display", serif; font-weight: 700;
    font-size: 58px; line-height: 1; color: var(--title-grey); letter-spacing: -1px;
  }
  .product {
    top: 262px; font-family: "Cinzel", serif; font-weight: 600;
    font-size: 40px; line-height: 1; color: var(--honey); letter-spacing: 1px;
  }
  .ingredients {
    top: 322px; font-family: "Pirata One", cursive; font-size: 27px;
    line-height: 33px; color: var(--copy-grey);
  }
  .phone {
    top: 392px; display: flex; align-items: center; justify-content: center; gap: 12px;
    font-family: "Roboto", sans-serif; font-weight: 700; font-size: 27px; color: var(--honey);
  }
  .phone-icon { width: 32px; height: 36px; }
  .company {
    top: 430px; font-family: "Pirata One", cursive; font-size: 27px; color: var(--copy-grey);
  }
</style>
</head>
<body>
<div class="canvas">
  <section class="label">
    <svg class="label-frame" width="1012" height="506" viewBox="0 0 1012 506" aria-hidden="true">
      <g fill="none" stroke="var(--frame)">
        <rect x="37" y="16" width="938" height="474" stroke-width="1"/>
        <rect x="43" y="22" width="926" height="462" stroke-width="2" stroke-dasharray="2 2"/>
        <rect x="49" y="28" width="914" height="450" stroke-width="1"/>
        <line x1="16" y1="37" x2="16" y2="469" stroke-width="1"/>
        <line x1="996" y1="37" x2="996" y2="469" stroke-width="1"/>
        <line x1="22" y1="40" x2="22" y2="466" stroke-width="2" stroke-dasharray="2 2"/>
        <line x1="990" y1="40" x2="990" y2="466" stroke-width="2" stroke-dasharray="2 2"/>
      </g>
      <g fill="var(--ornament)" role="img" aria-label="Corner flourishes">
        <rect x="6" y="6" width="36" height="36" rx="14"/>
        <rect x="970" y="6" width="36" height="36" rx="14"/>
        <rect x="6" y="464" width="36" height="36" rx="14"/>
        <rect x="970" y="464" width="36" height="36" rx="14"/>
      </g>
    </svg>

    <div class="comb-area comb-area--top" role="img" aria-label="Embossed honeycomb pattern"
         style="background: radial-gradient(ellipse at 45% 45%, var(--comb-edge), var(--comb) 60%, transparent 75%);"></div>
    <div class="comb-area comb-area--bottom" role="img" aria-label="Embossed honeycomb pattern"
         style="background: radial-gradient(ellipse at 55% 55%, var(--comb-edge), var(--comb) 60%, transparent 75%);"></div>

    <div class="brand"><span class="brand-dot"></span>Amber Comb</div>

    <h1 class="text-block title">GOURMET</h1>
    <h2 class="text-block product">CANDIED PECANS</h2>
    <p class="text-block ingredients">Made with Cinnamon<br>Brown Sugar &amp; Salt Order More</p>
    <p class="text-block phone">
      <svg class="phone-icon" viewBox="0 0 32 36" aria-hidden="true">
        <polygon points="16,0 32,9 32,27 16,36 0,27 0,9" fill="var(--honey)"/>
        <path d="M10 10c2-1 3 0 4 2l1 2c0 1-1 2-2 2 1 3 3 5 6 6 0-1 1-2 2-2l2 1c2 1 3 2 2 4-1 2-3 3-5 2-5-2-9-6-11-11-1-2 0-4 1-6z" fill="var(--label-bg)"/>
      </svg>
      (555)014-2738
    </p>
    <p class="text-block company">Amber Comb Market, LLC</p>
  </section>
</div>
</body>
</html>
```